Heron Property Inspection business card

I am the principal inspector of Heron Property Inspections. I serve Northern Virginia from Winchester to Arlington.Associate, Federated Guild of Dwelling Examiners (FGDE)Graduate, FGDE Home Inspectors CourseNational Association of Home Inspectors ExamI'd like the business card to look more professional than comical.I pulled the attached picture off the web. I'd like to have something like that or an image of a house as my logo on the cards.

Target Market(s)

Persons who recently purchased a home.

Industry/Entity Type

Business

Contact Information for Business Card

Heron Property Inspections, LLC.4455 River RoadBluemont, Virginia 20135cell: 703-231-6680e-mail: tkmarlow@postvale.net

Font styles to use
Serif
Sans Serif

Requirements
Must have
• I'd like to have a logo, something that identifies me as a home inspector. The attached images are something that I'd like to have incorporated into my business card logo.
Nice to have
• I'd like a sketch of a house and/or a magnifying glass showing a house being inspected. The attached images are used as a suggestion only, I do not own the images.
Should not have
• Gimmicky stuff. I want to appear professional and trustworthy.

```html
<!DOCTYPE html>
<html lang="en">
<head>
<meta charset="utf-8">
<title>Heron Property Inspections – Business Card</title>
<link rel="stylesheet" href="https://fonts.googleapis.com/css2?family=Open+Sans:wght@400;600&display=swap">
<style>
  :root {
    --canvas: #e7e5e1;
    --card-top: #1d1d1f;
    --card-bottom: #050505;
    --ink: #f4f4f4;
    --ink-soft: #cfcfcf;
    --accent: #d3232a;
    --rule: #6b6b6b;
  }
  * { box-sizing: border-box; margin: 0; padding: 0; }
  html, body { width: 1200px; height: 892px; overflow: hidden; }
  body {
    background: var(--canvas);
    font-family: "Open Sans", Arial, sans-serif;
    display: flex;
    align-items: center;
    justify-content: center;
    gap: 48px;
  }
  .card {
    width: 530px;
    height: 303px;
    border-radius: 4px;
    background: linear-gradient(160deg, var(--card-top), var(--card-bottom) 70%);
    box-shadow: 0 10px 28px rgba(0,0,0,.28);
    position: relative;
    color: var(--ink);
  }
  /* front */
  .card--front {
    display: flex;
    align-items: center;
    justify-content: center;
  }
  .brand {
    display: flex;
    align-items: center;
    gap: 16px;
  }
  .brand__mark {
    width: 22px;
    height: 22px;
    background: var(--accent);
    flex: none;
  }
  .brand__name {
    font-weight: 600;
    font-size: 27px;
    letter-spacing: .01em;
    color: var(--ink);
    line-height: 1.2;
  }
  /* back */
  .card--back { padding: 58px 0 0 66px; }
  .person__name {
    font-size: 40px;
    font-weight: 600;
    line-height: 1.05;
  }
  .person__title {
    font-size: 15px;
    color: var(--ink-soft);
    margin-top: 6px;
  }
  .contact {
    list-style: none;
    margin-top: 34px;
    display: grid;
    gap: 7px;
  }
  .contact__item {
    display: flex;
    align-items: flex-start;
    gap: 14px;
    font-size: 17px;
    line-height: 1.2;
  }
  .contact__icon {
    width: 18px;
    height: 18px;
    border-radius: 3px;
    background: var(--accent);
    flex: none;
    margin-top: 2px;
  }
  .contact__icon svg { display: block; width: 18px; height: 18px; }
</style>
</head>
<body>

  <section class="card card--front" aria-label="Card front">
    <div class="brand">
      <span class="brand__mark"></span>
      <span class="brand__name">Heron Property Inspections, LLC</span>
    </div>
  </section>

  <section class="card card--back" aria-label="Card back">
    <h1 class="person__name">Employee name</h1>
    <p class="person__title">Managing Director</p>
    <ul class="contact">
      <li class="contact__item">
        <span class="contact__icon">
          <svg viewBox="0 0 18 18"><rect x="5.5" y="3.5" width="7" height="11" rx="1.2" fill="none" stroke="#fff" stroke-width="1.4"/><circle cx="9" cy="12.3" r=".8" fill="#fff"/></svg>
        </span>
        <span>703-555-0192</span>
      </li>
      <li class="contact__item">
        <span class="contact__icon">
          <svg viewBox="0 0 18 18"><rect x="3.5" y="5" width="11" height="8" fill="none" stroke="#fff" stroke-width="1.3"/><path d="M3.5 5 9 9.6 14.5 5" fill="none" stroke="#fff" stroke-width="1.3"/></svg>
        </span>
        <span>tkmarlow@postvale.net</span>
      </li>
      <li class="contact__item">
        <span class="contact__icon">
          <svg viewBox="0 0 18 18"><path d="M9 15s-4-4.3-4-7.2a4 4 0 0 1 8 0C13 10.7 9 15 9 15z" fill="#fff"/><circle cx="9" cy="7.8" r="1.5" fill="#d3232a"/></svg>
        </span>
        <span>7182 Quarry LaneFernhill,<br>Fernhill, Virginia 20148</span>
      </li>
    </ul>
  </section>

</body>
</html>
```